Business card for law firm

Need business card for new law firm. Think confident, authoritative, conservative, but not stuffy or old-fashioned.

Contact Information for Business Card

Content for card - logo (uploaded), plus the following:

Paul Whitcombe (larger font)
Managing Partner (larger font, but not as large as name)
Level 9, 7 Ferris Lane
Sydney NSW 2000
Main Tel 02 9364 2710
Direct Tel 02 8472 3159
Email paul@qvlegal.com.au
www.qvlegal.com.au

Letterhead design should include logo plus:
Level 9, 7 Ferris Lane
Sydney NSW 2000
Tel 02 8472 3159
www.qvlegal.com.au

```html
<!DOCTYPE html>
<html lang="en">
<head>
<meta charset="utf-8">
<title>Quayvale Lawyers – Business Card</title>
<link rel="stylesheet" href="https://fonts.googleapis.com/css2?family=Roboto:wght@400;500;700&display=swap">
<style>
  :root {
    --navy: #031c56;
    --ink: #111111;
    --text-grey: #4a4a4a;
    --rule: #7a7a7a;
    --paper: #ffffff;
    --backdrop: #e3e3e3;
  }
  * { box-sizing: border-box; margin: 0; padding: 0; }
  html, body { width: 1125px; height: 1200px; overflow: hidden; }
  body {
    background: var(--backdrop);
    font-family: "Roboto", Arial, sans-serif;
    position: relative;
  }
  .card {
    position: absolute;
    left: 171px;
    width: 826px;
    height: 472px;
    overflow: hidden;
  }
  .card--front { top: 106px; background: var(--paper); }
  .card--back { top: 639px; background: var(--navy); }

  /* Brand block */
  .brand-mark {
    position: absolute;
    left: 610px; top: 60px;
    width: 66px; height: 66px;
    background: var(--navy);
  }
  .brand {
    position: absolute;
    right: 41px; top: 176px;
    text-align: center;
    color: var(--ink);
    font-weight: 400;
  }
  .brand__name { display: block; font-size: 43px; letter-spacing: 1px; line-height: 1; }
  .brand__type { display: block; font-size: 17px; letter-spacing: 15px; margin-right: -15px; margin-top: 8px; line-height: 1; }

  /* Person */
  .person { position: absolute; left: 41px; top: 265px; }
  .person__name { font-size: 32px; font-weight: 700; color: var(--navy); line-height: 1; text-transform: uppercase; }
  .person__role { font-size: 21px; font-weight: 500; color: var(--ink); line-height: 1; margin-top: 7px; text-transform: uppercase; }

  .divider {
    position: absolute;
    left: 41px; right: 41px; top: 334px;
    height: 1.5px; background: var(--rule);
  }

  .contacts {
    position: absolute; left: 41px; top: 352px;
    list-style: none;
    font-size: 20px; color: var(--text-grey);
  }
  .contacts li { display: flex; align-items: center; height: 26.5px; }
  .contacts svg { width: 18px; height: 18px; margin-right: 12px; fill: var(--navy); }

  .address {
    position: absolute; right: 41px; top: 352px;
    text-align: right; font-size: 20px; color: var(--text-grey);
    font-style: normal;
  }
  .address span { display: block; height: 26.5px; line-height: 26.5px; }
  .address .web { letter-spacing: 1.5px; }

  .base-band {
    position: absolute; left: 0; right: 0; bottom: 0;
    height: 13px; background: var(--navy);
  }

  /* Back */
  .brand--reverse { color: var(--paper); top: 311px; right: 75px; }
  .brand--reverse .brand__name { font-size: 45px; }
  .back-web {
    position: absolute; right: 72px; top: 396px;
    color: var(--paper); font-size: 20px; letter-spacing: 7px;
  }
</style>
</head>
<body>
  <section class="card card--front">
    <div class="brand-mark"></div>
    <div class="brand">
      <span class="brand__name">QUAYVALE</span>
      <span class="brand__type">LAWYERS</span>
    </div>

    <div class="person">
      <p class="person__name">Paul Whitcombe</p>
      <p class="person__role">Managing Partner</p>
    </div>

    <div class="divider"></div>

    <ul class="contacts">
      <li>
        <svg viewBox="0 0 24 24" aria-hidden="true"><path d="M6.6 10.8a15.1 15.1 0 0 0 6.6 6.6l2.2-2.2c.3-.3.7-.4 1-.2 1.1.4 2.3.6 3.6.6.6 0 1 .4 1 1V20c0 .6-.4 1-1 1A17 17 0 0 1 3 4c0-.6.4-1 1-1h3.5c.6 0 1 .4 1 1 0 1.3.2 2.5.6 3.6.1.3 0 .7-.2 1z"/></svg>
        02 9364 2710
      </li>
      <li>
        <svg viewBox="0 0 24 24" aria-hidden="true"><path d="M6.6 10.8a15.1 15.1 0 0 0 6.6 6.6l2.2-2.2c.3-.3.7-.4 1-.2 1.1.4 2.3.6 3.6.6.6 0 1 .4 1 1V20c0 .6-.4 1-1 1A17 17 0 0 1 3 4c0-.6.4-1 1-1h3.5c.6 0 1 .4 1 1 0 1.3.2 2.5.6 3.6.1.3 0 .7-.2 1z"/></svg>
        02 8472 3159
      </li>
      <li>
        <svg viewBox="0 0 24 24" aria-hidden="true"><path d="M2 6h20v12H2z M3.5 7.5 12 13l8.5-5.5" fill="none" stroke="#031c56" stroke-width="2"/></svg>
        paul@qvlegal.com.au
      </li>
    </ul>

    <address class="address">
      <span>Level 9, 7 Ferris Lane</span>
      <span>Sydney NSW 2000</span>
      <span class="web">www.qvlegal.com.au</span>
    </address>

    <div class="base-band"></div>
  </section>

  <section class="card card--back">
    <div class="brand brand--reverse">
      <span class="brand__name">QUAYVALE</span>
      <span class="brand__type">LAWYERS</span>
    </div>
    <p class="back-web">www.qvlegal.com.au</p>
  </section>
</body>
</html>
```